Government contracting small business needs a web design

Tarvex Summit Inc is a veteran owned small business that delivers a full range of professional services as well as training in information technology, security and defense intelligence solutions.
We need a professional/corporate looking website where potential clients can view what services are offered.
This being a new company, there is not much that can added more than a narrative statement, stock photos and a place where potential customers and employees can make contact.
Open to ideas.
Target Market(s)
US Government
Industry/Entity Type
Small Business
Look and feel
Each slider illustrates characteristics of the customer's brand and the style your logo design should communicate.

```html
<!DOCTYPE html>
<html lang="en">
<head>
<meta charset="utf-8">
<title>Tarvex Summit Inc</title>
<link rel="stylesheet" href="https://fonts.googleapis.com/css2?family=PT+Sans:wght@400;700&display=swap">
<style>
  :root {
    --page: #ffffff;
    --panel: #f1f1f1;
    --rule: #c9c9c9;
    --text: #3a3a3a;
    --heading: #3c3c3c;
    --gold: #d4a52a;
    --accent: #c9862a;
    --nav-top: #8a8a8a;
    --nav-bottom: #4c4c4c;
    --nav-active-top: #f4d25a;
    --nav-active-bottom: #d9a520;
    --footer-top: #8c8c8c;
    --footer-bottom: #585858;
    --bullet: #4a4a4a;
  }
  * { box-sizing: border-box; margin: 0; padding: 0; }
  html, body { width: 1200px; height: 1167px; overflow: hidden; background: var(--page); }
  body { position: relative; font-family: "PT Sans", sans-serif; color: var(--text); }

  .brand { position: absolute; left: 35px; top: 56px; display: flex; align-items: center; gap: 12px; }
  .brand-mark { width: 48px; height: 48px; border-radius: 50%; background: var(--gold); }
  .brand-name { font-size: 38px; font-weight: 700; color: #5a5a5a; letter-spacing: 0.5px; }

  .main-nav { position: absolute; left: 414px; top: 63px; width: 759px; height: 37px; display: flex; }
  .main-nav a {
    display: flex; align-items: center; justify-content: center;
    height: 100%; color: #fff; text-decoration: none; font-size: 15px; letter-spacing: 0.3px;
    background: linear-gradient(var(--nav-top), var(--nav-bottom));
    border-left: 1px solid #d8d8d8;
  }
  .main-nav a.active { background: linear-gradient(var(--nav-active-top), var(--nav-active-bottom)); color: #3a3a3a; border-left: none; }

  .hero { position: absolute; left: 29px; top: 120px; width: 1144px; height: 394px; border: 1px solid #dcdcdc; background: var(--panel); overflow: hidden; }
  .hero-photo { position: absolute; left: 0; top: 0; width: 680px; height: 100%;
    background: radial-gradient(ellipse at 40% 50%, #9aa6b8 0%, #d9dde4 45%, var(--panel) 80%); }
  .hero-title { position: absolute; right: 35px; top: 163px; text-align: right; line-height: 1; }
  .hero-title .big { font-size: 54px; color: var(--gold); }
  .hero-title .and { font-size: 34px; color: var(--gold); }
  .hero-title .sub { display: block; margin-top: 6px; font-size: 33px; color: #4a4a4a; }

  .features { position: absolute; left: 0; top: 543px; width: 1200px; height: 351px; background: var(--panel); border-bottom: 1px solid var(--rule); }
  .feature { position: absolute; top: 0; height: 100%; }
  .feature + .feature { border-left: 1px solid var(--rule); }
  .feature h2 { position: absolute; top: 21px; font-size: 24px; font-weight: 400; color: var(--heading); white-space: nowrap; }
  .feature-photo { position: absolute; top: 54px; width: 337px; height: 126px; }
  .feature p { position: absolute; top: 195px; width: 340px; font-size: 15px; line-height: 19.8px; }
  .more { position: absolute; font-size: 15px; font-weight: 700; color: var(--accent); text-decoration: none; }
  .feature .more { top: 316px; }

  .service-list { position: absolute; top: 76px; left: 46px; list-style: none; }
  .service-list li { height: 34px; font-size: 15px; display: flex; align-items: center; }
  .service-list li::before { content: ""; width: 8px; height: 8px; background: var(--bullet); transform: rotate(45deg); margin-right: 15px; }

  .intro { position: absolute; left: 44px; top: 920px; width: 1115px; font-size: 15px; line-height: 25.7px; }

  .site-footer { position: absolute; left: 29px; top: 1080px; width: 1144px; height: 87px; background: linear-gradient(var(--footer-top), var(--footer-bottom)); }
  .copyright { position: absolute; left: 29px; top: 35px; font-size: 12.5px; color: #fff; }
  .social { position: absolute; top: 35px; display: flex; gap: 23px; left: 984px; }
  .social span { width: 18px; height: 18px; border-radius: 2px; }
</style>
</head>
<body>
  <header>
    <div class="brand"><span class="brand-mark"></span><span class="brand-name">Tarvex Summit</span></div>
    <nav class="main-nav">
      <a href="#" class="active" style="width:123px">HOME</a>
      <a href="#" style="width:154px">ABOUT US</a>
      <a href="#" style="width:163px">SOLUTIONS</a>
      <a href="#" style="width:151px">SERVICES</a>
      <a href="#" style="width:168px">CONTACT US</a>
    </nav>
  </header>

  <section class="hero">
    <div class="hero-photo" role="img" aria-label="Combination padlock wrapped in blue network cables"></div>
    <h1 class="hero-title"><span class="big">IT SECURITY</span> <span class="and">AND</span><span class="sub">INTELLIGENCE SOLUTIONS</span></h1>
  </section>

  <section class="features">
    <div class="feature" style="left:0;width:399px">
      <h2 style="left:30px">IT SECURITY</h2>
      <div class="feature-photo" role="img" aria-label="Hands holding a globe beside web keys" style="left:29px;background:linear-gradient(90deg,#3f7fc4,#8fc0e6 55%,#2f5f9e)"></div>
      <p style="left:30px">Lorem Ipsum is simply dummy text of the printing and typesetting industry. Lorem Ipsum has been the industry's standard dummy text ever since the 1500s, when an unknown printer took a galley type specimen book.</p>
      <a href="#" class="more" style="right:35px">more</a>
    </div>
    <div class="feature" style="left:399px;width:401px">
      <h2 style="left:33px">INTELLIGENCE SOLUTIONS</h2>
      <div class="feature-photo" role="img" aria-label="Hand moving a chess piece on a board" style="left:32px;background:linear-gradient(90deg,#efe6d8,#c9b8a4 50%,#e4ddd4)"></div>
      <p style="left:33px">Lorem Ipsum is simply dummy text of the printing and typesetting industry. Lorem Ipsum has been the industry's standard dummy text ever since the 1500s, when an unknown printer took a galley type specimen book.</p>
      <a href="#" class="more" style="right:33px">more</a>
    </div>
    <div class="feature" style="left:800px;width:400px">
      <h2 style="left:37px">SERVICES</h2>
      <ul class="service-list">
        <li>Lorem Ipsum is simply dummy</li>
        <li>Lorem Ipsum is simply</li>
        <li>Lorem Ipsum is</li>
        <li>Lorem Ipsum is simply</li>
        <li>Lorem Ipsum is simply dummy</li>
        <li>Lorem Ipsum is simply</li>
        <li>Lorem Ipsum is simply dummy</li>
      </ul>
      <a href="#" class="more" style="right:47px">more</a>
    </div>
  </section>

  <p class="intro">Lorem Ipsum is simply dummy text of the printing and typesetting industry. Lorem Ipsum has been the industry's standard dummy text ever since the 1500s, when an unknown printer took a galley type specimen book. the printing and typesetting industry. Lorem Ipsum has been the industry's standard dummy text ever since the 1500s, when an unknown printer took a galley type specimen book. the printing and typesetting industry. Lorem Ipsum has been the industry's standard dummy text ever since the 1500s, when an unknown printer took a galley type specimen book. the printing and typesetting industry. Lorem Ipsum has been the industry's standard dummy text ever since the 1500s, when an unknown printer took a galley type specimen book.</p>
  <a href="#" class="more" style="right:47px;top:1056px">more</a>

  <footer class="site-footer">
    <p class="copyright">©2012 Tarvex Summit. All Rights Reserved.</p>
    <div class="social">
      <span style="background:#39b5e6"></span>
      <span style="background:#3b5da8"></span>
      <span style="background:#1a7ab0"></span>
      <span style="background:#f08a1c"></span>
    </div>
  </footer>
</body>
</html>
```